Briloran Clear Springs needs a new business card design (we produce and sell pure bottled water)

We need a clean modern design for our new business cards, We have an existing logo which ultimately cannot be changed, however it could be slighty improved and the colours adjusted. We have this existing logo on all of our bottles, vehicles etc.

Our company slogan is "Pure down to the last drop".
Along with our relevant company information
(Address, phone, website email etc) we will only be using names and not putting position titles for flexibilty.

We are looking for a clean, minimalist modern design.

You can view our website (if need of an update also!) to see our business.

Industry/Entity Type

Business

Contact Information for Business Card

Staff Name : XXXXXX XXXXXX
Address : 9/41 Tavenor St
Halden Rise QLD 4172
Staff Mobile Number : 04XX XXX XXX
Office Phone Number : 07 3918 2457
Staff Email Address : XXXX@brilorancleargo.com.au
Website : www.brilorancleargo.com.au

Font styles to use
Sans Serif

Colors
cee9f5
33a6d7
0492cd
0455a3
3276b5
85abd2
cedeed

Requirements
Must have
• The ability to edit and change the staff members details as we will need to edit for each respective staff member (7 in total)

```html
<!DOCTYPE html>
<html lang="en">
<head>
<meta charset="utf-8">
<title>Briloran Clear Springs – Business Card</title>
<link href="https://fonts.googleapis.com/css2?family=Open+Sans:wght@400;700;800&display=swap" rel="stylesheet">
<style>
  :root {
    --page-bg: #e9ecef;
    --card-white: #ffffff;
    --card-black: #1b1b1b;
    --brand-blue: #0455a3;
    --brand-mid: #3276b5;
    --ink: #222222;
  }
  * { margin: 0; padding: 0; box-sizing: border-box; }
  html, body { width: 1200px; height: 900px; overflow: hidden; }
  body {
    background: var(--page-bg);
    font-family: "Open Sans", Arial, sans-serif;
    position: relative;
  }
  .card {
    position: absolute;
    left: 250px;
    width: 700px;
    height: 400px;
    overflow: hidden;
    box-shadow: 0 6px 18px rgba(0,0,0,0.18);
  }
  .card-back { top: 35px; background: var(--card-black); }
  .card-front { top: 465px; background: var(--card-white); }

  .brand {
    position: absolute;
    display: flex;
    align-items: center;
    gap: 12px;
    color: var(--brand-blue);
    font-weight: 800;
    text-transform: uppercase;
    line-height: 1;
  }
  .brand-dot {
    width: 18px; height: 18px;
    border-radius: 50%;
    background: var(--brand-blue);
    flex: none;
  }
  .card-back .brand { left: 50%; top: 50%; transform: translate(-50%, -50%); font-size: 30px; }
  .card-front .brand { right: 50px; top: 180px; font-size: 24px; }

  .decor { position: absolute; inset: 0; }

  .staff-name {
    position: absolute;
    left: 62px; top: 34px;
    color: var(--brand-blue);
    font-weight: 700;
    font-size: 18px;
  }
  .address {
    position: absolute;
    left: 62px; top: 142px;
    font-size: 14px;
    line-height: 18px;
    color: var(--ink);
  }
  .contacts {
    position: absolute;
    left: 44px; top: 196px;
    list-style: none;
    font-size: 14px;
    line-height: 18px;
    color: var(--ink);
  }
  .contacts li { display: flex; align-items: center; gap: 8px; }
  .contacts svg { width: 11px; height: 11px; flex: none; fill: var(--brand-blue); }
</style>
</head>
<body>

<section class="card card-back" aria-label="Card back">
  <div class="brand"><span class="brand-dot"></span>Briloran Clear Springs</div>
</section>

<section class="card card-front" aria-label="Card front">
  <svg class="decor" viewBox="0 0 700 400" aria-hidden="true">
    <polygon points="0,0 40,0 0,30" fill="var(--brand-blue)"/>
    <polygon points="40,0 48,0 48,34 6,34" fill="var(--card-black)"/>
    <polygon points="0,310 300,330 290,345 0,330" fill="var(--brand-blue)"/>
    <polygon points="300,338 700,338 700,400 258,400" fill="var(--card-black)"/>
  </svg>

  <h1 class="staff-name">Marcus Tellwin</h1>

  <address class="address" style="font-style:normal">
    9/41 Tavenor St<br>
    Halden Rise QLD 4172
  </address>

  <ul class="contacts">
    <li><svg viewBox="0 0 10 10"><rect x="2.5" y="0" width="5" height="10" rx="1"/></svg>0400 586 213</li>
    <li><svg viewBox="0 0 10 10"><path d="M1 1 L3.5 0.5 L4.5 3 L3 4 Q4 6 6 7 L7 5.5 L9.5 6.5 L9 9 Q3 9 1 1 Z"/></svg>07 3918 2457</li>
    <li><svg viewBox="0 0 10 10"><rect x="0" y="2" width="10" height="6.5"/></svg>info@brilorancleargo.com.au</li>
    <li><svg viewBox="0 0 10 10"><circle cx="5" cy="5" r="5"/></svg>www.brilorancleargo.com.au</li>
  </ul>

  <div class="brand"><span class="brand-dot"></span>Briloran Clear Springs</div>
</section>

</body>
</html>
```